SOLVE Study flyer

I need help designing a flyer for a research study that will include brain imaging in adolescents. The info is in the attached document. The study is called the Sequoia Outlook Lantern Valley Echo (SOLVE) study. Ideally this would be returned as a document that I can edit in the future as we will have several new recruitment phases (different age groups, etc. I also would love to have a logo designed as part of this project, but I recognize that might be a separate design request.

```html
<!DOCTYPE html>
<html lang="en">
<head>
<meta charset="utf-8">
<title>SOLVE Study Flyer</title>
<link rel="stylesheet" href="https://fonts.googleapis.com/css2?family=Oswald:wght@500;600;700&family=Poppins:wght@400;500&display=swap">
<style>
  :root {
    --royal: #0a3b8f;
    --royal-deep: #062f7d;
    --navy: #031c55;
    --gold: #f8c51c;
    --paper: #ebebeb;
    --ink: #111111;
    --white: #ffffff;
    --photo-light: #dfe5ef;
    --photo-mid: #9aaec8;
  }
  * { margin: 0; padding: 0; box-sizing: border-box; }
  html, body { width: 890px; height: 1200px; overflow: hidden; background: var(--paper); }
  .flyer {
    position: relative;
    width: 890px;
    height: 1200px;
    overflow: hidden;
    background: var(--paper);
    font-family: "Poppins", sans-serif;
    color: var(--white);
  }
  .flyer-shapes, .study-photo { position: absolute; left: 0; top: 0; }
  .fill-royal { fill: var(--royal); }
  .fill-deep { fill: var(--royal-deep); }
  .fill-navy { fill: var(--navy); }
  .fill-white { fill: var(--white); }

  .study-title {
    position: absolute;
    left: 486px;
    top: 24px;
    font-family: "Oswald", sans-serif;
    font-weight: 600;
    font-size: 36px;
    line-height: 40px;
    color: var(--ink);
    letter-spacing: -0.2px;
  }

  .headline-rule {
    position: absolute;
    left: 38px;
    top: 54px;
    width: 156px;
    height: 3px;
    background: var(--white);
  }
  .headline {
    position: absolute;
    left: 38px;
    top: 78px;
    font-family: "Oswald", sans-serif;
    font-weight: 600;
    font-size: 50px;
    line-height: 56px;
    text-transform: uppercase;
    text-shadow: 0 2px 4px rgba(0, 0, 0, 0.35);
  }
  .headline .ask { color: var(--gold); display: block; }
  .headline .question { color: var(--white); display: block; }

  .intro {
    position: absolute;
    left: 39px;
    top: 572px;
    font-size: 16.5px;
    font-weight: 500;
    line-height: 23.5px;
    white-space: nowrap;
  }

  .section-heading {
    position: absolute;
    left: 38px;
    font-family: "Oswald", sans-serif;
    font-weight: 500;
    font-size: 24px;
    line-height: 26px;
    color: var(--gold);
  }
  .section-heading.involves { top: 745px; }
  .section-heading.eligible { top: 1001px; }

  .checklist {
    position: absolute;
    left: 38px;
    list-style: none;
    font-size: 16px;
    font-weight: 500;
    line-height: 20px;
    white-space: nowrap;
  }
  .checklist.involves { top: 790px; }
  .checklist.eligible { top: 1033px; }
  .checklist li {
    position: relative;
    padding-left: 34px;
    margin-bottom: 7px;
  }
  .checklist li::before {
    content: "";
    position: absolute;
    left: 5px;
    top: 2px;
    width: 16px;
    height: 16px;
    border-radius: 50%;
    background: var(--white);
  }
  .checklist li::after {
    content: "";
    position: absolute;
    left: 10.5px;
    top: 5px;
    width: 4px;
    height: 7px;
    border: solid var(--royal);
    border-width: 0 2px 2px 0;
    transform: rotate(45deg);
  }

  .contact-call {
    position: absolute;
    right: 24px;
    top: 842px;
    text-align: right;
    font-family: "Oswald", sans-serif;
    font-weight: 500;
    font-size: 27px;
    line-height: 35px;
    text-transform: uppercase;
  }
  .contact-call .lead { color: var(--gold); display: block; }
  .contact-call .follow { color: var(--white); display: block; }

  .contact-email {
    position: absolute;
    right: 24px;
    top: 1024px;
    display: flex;
    align-items: center;
    gap: 10px;
    font-size: 22px;
    font-weight: 500;
    letter-spacing: 0.6px;
    text-shadow: 0 2px 3px rgba(0, 0, 0, 0.4);
  }
  .contact-email svg { fill: var(--gold); }

  .compensation {
    position: absolute;
    right: 24px;
    top: 1068px;
    text-align: right;
    font-family: "Oswald", sans-serif;
    font-weight: 700;
    font-size: 56px;
    line-height: 56px;
    color: var(--gold);
    text-shadow: 0 3px 4px rgba(0, 0, 0, 0.35);
  }
</style>
</head>
<body>
<main class="flyer">
  <svg class="flyer-shapes" width="890" height="1200" viewBox="0 0 890 1200" aria-hidden="true">
    <path class="fill-white" d="M390 0 H890 V132 Q860 140 810 140 H482 Q452 140 436 112 L390 0 Z"/>
    <path class="fill-deep" d="M0 0 H363 L450 165 Q470 205 450 245 L332 505 Q314 540 270 540 H0 Z"/>
    <path class="fill-royal" d="M0 556 H262 Q300 556 320 586 L495 880 Q511 910 495 940 L339 1200 H0 Z"/>
    <path class="fill-deep" d="M598 189 H890 V812 H506 Q480 812 468 788 L350 470 Q340 441 354 412 L562 208 Q580 189 598 189 Z"/>
    <path class="fill-navy" d="M522 836 H890 V1014 H346 L472 858 Q490 836 522 836 Z"/>
    <path class="fill-deep" d="M346 1014 H890 V1200 H379 Z"/>
  </svg>

  <svg class="study-photo" width="890" height="1200" viewBox="0 0 890 1200" role="img" aria-label="Photo of two smiling teenage girls reviewing papers and a tablet together">
    <defs>
      <linearGradient id="photoTone" x1="0" y1="0" x2="1" y2="1">
        <stop offset="0" stop-color="#eef1f6"/>
        <stop offset="0.55" stop-color="#c3cfdf"/>
        <stop offset="1" stop-color="#6e86ab"/>
      </linearGradient>
    </defs>
    <path fill="url(#photoTone)" d="M614 189 H890 V812 H520 Q496 812 486 790 L370 472 Q360 441 374 412 L578 208 Q594 189 614 189 Z"/>
  </svg>

  <h2 class="study-title">Sequoia Outlook Lantern<br>Valley Echo</h2>

  <div class="headline-rule"></div>
  <h1 class="headline">
    <span class="ask">Are you the</span>
    <span class="ask">parent of a child</span>
    <span class="ask">age 10-17 ?</span>
    <span class="question">Do they worry</span>
    <span class="question">or overthink</span>
    <span class="question">negative</span>
    <span class="question">emotions ?</span>
  </h1>

  <p class="intro">
    Ridgeline University<br>
    researchers are seeking girls<br>
    age 10-17 for a study about<br>
    brain activity in emotions and<br>
    decision-making and how they<br>
    relate to puberty, anxiety and<br>
    depression.
  </p>

  <h3 class="section-heading involves">Study Participation Involves:</h3>
  <ul class="checklist involves">
    <li>One one-hour interview<br>(online or in-person) where your child<br>will discuss their thoughts</li>
    <li>Online questionnaires (parent and child)</li>
    <li>One two-hour visit where your child will<br>complete an MRI scan, answer questions<br>about their puberty stage, and have a<br>small hair sample taken to study<br>puberty hormones</li>
  </ul>

  <h3 class="section-heading eligible">Your Child may be Eligible if they:</h3>
  <ul class="checklist eligible">
    <li>Are age 10-17</li>
    <li>Tend to worry or overthink<br>negative thoughts</li>
    <li>Have not been diagnosed<br>with psychosis, learning<br>problems, or autism</li>
  </ul>

  <p class="contact-call">
    <span class="lead">Interested in</span>
    <span class="lead">participating?</span>
    <span class="follow">Want more information?</span>
    <span class="follow">Please contact us!</span>
  </p>

  <p class="contact-email">
    solvestudy@ridgeline.edu
    <svg width="20" height="14" viewBox="0 0 20 14" aria-hidden="true">
      <path d="M0 0 H20 V14 H0 Z M1.5 1.5 L10 8 L18.5 1.5 Z" fill-rule="evenodd"/>
    </svg>
  </p>

  <p class="compensation">Compensation<br>up to $140</p>
</main>
</body>
</html>
```